New Business Card Design Project

We would like a business card that represents the sale of boat, home, auto, and life insurance.

The logo can change colors to meet the look of the design if needed.

Industry/Entity Type

Business

```html
<!DOCTYPE html>
<html lang="en">
<head>
<meta charset="utf-8">
<title>Alder Financial — Business Cards</title>
<link rel="stylesheet" href="https://fonts.googleapis.com/css2?family=Questrial&family=Open+Sans:wght@400;700&display=swap">
<style>
  :root {
    --backdrop: #3b322e;
    --card: #f6f6f4;
    --ink: #2b2b2b;
    --ink-soft: #3c3c3c;
    --green: #77943a;
    --green-light: #8aa64a;
    --faint: #e6e6e4;
    --white: #ffffff;
  }
  * { margin: 0; padding: 0; box-sizing: border-box; }
  html, body {
    width: 1200px; height: 768px; overflow: hidden;
    background: var(--backdrop);
  }
  .stage { position: relative; width: 1200px; height: 768px; }
  .card {
    position: absolute; top: 229px;
    width: 540px; height: 310px;
    background: var(--card);
    overflow: hidden;
    box-shadow: 0 10px 28px rgba(0,0,0,.35);
  }
  .card--front { left: 40px; }
  .card--back  { left: 620px; }

  .brand {
    position: absolute;
    display: flex; flex-direction: column; align-items: flex-start;
    font-family: "Questrial", sans-serif;
  }
  .brand__row { display: flex; align-items: center; gap: 10px; }
  .brand__dot {
    width: 22px; height: 22px; border-radius: 50%;
    background: var(--green);
  }
  .brand__name {
    font-family: "Questrial", sans-serif;
    font-size: 30px; letter-spacing: 5px;
    color: var(--ink); text-transform: uppercase; line-height: 1;
  }
  .brand__tagline {
    margin-top: 8px;
    font-family: "Questrial", sans-serif;
    font-size: 15px; letter-spacing: 1.5px; color: var(--ink-soft);
  }
  .card--front .brand { left: 120px; top: 112px; }
  .card--back .brand  { left: 70px;  top: 78px; }

  .card__art { position: absolute; inset: 0; }

  .holder {
    position: absolute; right: 28px; top: 104px; text-align: right;
    font-family: "Open Sans", sans-serif; color: var(--ink);
  }
  .holder__name { font-size: 16px; font-weight: 700; }
  .holder__role { font-size: 10px; margin-top: 2px; }

  .contact {
    position: absolute; right: 22px; top: 208px;
    list-style: none;
    font-family: "Open Sans", sans-serif; font-size: 11.5px;
    color: var(--white); text-align: right;
  }
  .contact__item {
    display: flex; justify-content: flex-end; align-items: center;
    gap: 8px; height: 17px;
  }
  .contact__icon { width: 11px; height: 11px; fill: var(--white); }
</style>
</head>
<body>
<main class="stage">

  <section class="card card--front" aria-label="Business card front">
    <div class="brand">
      <div class="brand__row">
        <span class="brand__dot"></span>
        <span class="brand__name">Alder Financial</span>
      </div>
      <span class="brand__tagline">investments &amp; insurance</span>
    </div>
  </section>

  <section class="card card--back" aria-label="Business card back">
    <svg class="card__art" viewBox="0 0 540 310" preserveAspectRatio="none" aria-hidden="true">
      <circle cx="120" cy="150" r="105" fill="none" stroke="var(--faint)" stroke-width="22"/>
      <path d="M0,168 C130,175 240,250 540,205 L540,310 L0,310 Z" fill="var(--green)"/>
      <path d="M0,150 C140,162 250,240 540,198 L540,205 C240,250 130,175 0,168 Z" fill="var(--white)"/>
      <path d="M20,132 C150,150 260,232 540,188" fill="none" stroke="var(--ink)" stroke-width="5"/>
      <path d="M10,118 C150,142 270,222 540,176" fill="none" stroke="var(--ink-soft)" stroke-width="3"/>
    </svg>

    <div class="brand">
      <div class="brand__row">
        <span class="brand__dot"></span>
        <span class="brand__name">Alder Financial</span>
      </div>
      <span class="brand__tagline">investments &amp; insurance</span>
    </div>

    <div class="holder">
      <p class="holder__name">Your Long Name</p>
      <p class="holder__role">Managing Director</p>
    </div>

    <ul class="contact">
      <li class="contact__item">00.00.00.0000
        <svg class="contact__icon" viewBox="0 0 12 12"><path d="M2 1h3l1 3-1.5 1a7 7 0 0 0 2.5 2.5L8 6l3 1v3c0 .6-.4 1-1 1A9 9 0 0 1 1 2c0-.6.4-1 1-1z"/></svg></li>
      <li class="contact__item">00.00.00.0000
        <svg class="contact__icon" viewBox="0 0 12 12"><rect x="1" y="5" width="10" height="6" rx="1"/><rect x="3" y="1" width="6" height="3"/></svg></li>
      <li class="contact__item">www.yourwebsite.com
        <svg class="contact__icon" viewBox="0 0 12 12"><circle cx="6" cy="6" r="5" fill="none" stroke="#fff" stroke-width="1.2"/><path d="M1 6h10M6 1v10" stroke="#fff" stroke-width="1"/></svg></li>
      <li class="contact__item">yourname@yourwebsite.com
        <svg class="contact__icon" viewBox="0 0 12 12"><rect x="1" y="2.5" width="10" height="7"/><path d="M1 2.5l5 4 5-4" fill="none" stroke="var(--green)" stroke-width="1"/></svg></li>
      <li class="contact__item">Your Commercial or office address
        <svg class="contact__icon" viewBox="0 0 12 12"><path d="M6 0.5a3.8 3.8 0 0 0-3.8 3.8C2.2 7 6 11.5 6 11.5S9.8 7 9.8 4.3A3.8 3.8 0 0 0 6 .5zm0 5.3a1.5 1.5 0 1 1 0-3 1.5 1.5 0 0 1 0 3z"/></svg></li>
    </ul>
  </section>

</main>
</body>
</html>
```